Business Card Design - Amberfield Court

We are looking at a new design for our business cards that has a modern and professional look. We run a residential aged care facility focussing on the care of residents. The cards will be used for potential clients, consultants and business opportunities in this sector. Blue and white is our main colours and would to see these colours incorporated in the design.
Industry/Entity Type
Business
Contact Information for Business Card
Amberfield Court, Darren Walsh, dwalsh@amberfieldcourt.com.au, Finance Manager, 0472 639 208, BCom, 37 Marrabel Crescent, Brindle Vale, Qld 4093.
Look and feel
Each slider illustrates characteristics of the customer's brand and the style your logo design should communicate.

```html
<!DOCTYPE html>
<html lang="en">
<head>
<meta charset="utf-8">
<title>Amberfield Court – Business Card</title>
<link rel="stylesheet" href="https://fonts.googleapis.com/css2?family=Open+Sans:wght@400;600;700&display=swap">
<style>
  :root {
    --backdrop: #2b2b2d;
    --steel-blue: #4a7f9c;
    --navy: #1e3a4a;
    --stone: #b3a99f;
    --white: #ffffff;
    --muted: #a9b4bb;
  }
  * { box-sizing: border-box; margin: 0; padding: 0; }
  html, body { width: 1200px; height: 900px; overflow: hidden; }
  body {
    background: var(--backdrop);
    font-family: "Open Sans", sans-serif;
    position: relative;
  }
  .card {
    position: absolute;
    width: 600px;
    height: 343px;
    border-radius: 22px;
    overflow: hidden;
  }
  .card-front {
    left: 180px;
    top: 90px;
    background: var(--steel-blue);
    display: flex;
    align-items: center;
    justify-content: center;
  }
  .brand {
    display: flex;
    align-items: center;
    gap: 14px;
  }
  .brand-dot {
    width: 22px;
    height: 22px;
    border-radius: 50%;
    background: var(--white);
  }
  .brand-name {
    font-weight: 600;
    font-size: 30px;
    letter-spacing: 3px;
    color: var(--white);
    text-transform: uppercase;
  }
  .card-back {
    left: 420px;
    top: 467px;
    background: var(--stone);
  }
  .card-back .swoosh {
    position: absolute;
    inset: 0;
    width: 100%;
    height: 100%;
  }
  .contact {
    position: absolute;
    left: 40px;
    top: 140px;
    color: var(--white);
  }
  .contact-name {
    font-weight: 700;
    font-size: 27px;
    letter-spacing: 0.5px;
    text-transform: uppercase;
    line-height: 1.1;
  }
  .contact-title {
    font-size: 12px;
    color: var(--muted);
    text-transform: uppercase;
    letter-spacing: 0.5px;
    margin-bottom: 12px;
  }
  .contact-line {
    display: flex;
    align-items: center;
    gap: 8px;
    font-size: 14px;
    line-height: 1.45;
  }
  .contact-line svg { width: 12px; height: 12px; flex: none; }
  .address {
    margin-top: 10px;
    margin-left: 20px;
    font-size: 14px;
    line-height: 1.35;
  }
  .back-brand {
    position: absolute;
    right: 26px;
    top: 118px;
    display: flex;
    align-items: center;
    gap: 8px;
  }
  .back-brand .brand-dot { width: 12px; height: 12px; background: var(--navy); }
  .back-brand .brand-name {
    font-size: 15px;
    letter-spacing: 1.5px;
    color: var(--navy);
    line-height: 1.2;
  }
</style>
</head>
<body>

  <section class="card card-front" aria-label="Card front">
    <div class="brand">
      <span class="brand-dot"></span>
      <span class="brand-name">Amberfield Court</span>
    </div>
  </section>

  <section class="card card-back" aria-label="Card back">
    <svg class="swoosh" viewBox="0 0 600 343" preserveAspectRatio="none" aria-hidden="true">
      <path fill="var(--steel-blue)" d="M0 0 H575 C505 30 500 160 455 240 C405 322 250 322 0 305 Z"/>
      <path fill="var(--navy)" d="M0 0 H545 C475 25 470 140 430 220 C390 298 250 300 0 285 Z"/>
      <path fill="var(--steel-blue)" d="M0 322 C150 325 300 322 380 343 H0 Z"/>
    </svg>

    <div class="contact">
      <p class="contact-name">Darren Walsh</p>
      <p class="contact-title">Finance Manager (BCom)</p>
      <p class="contact-line">
        <svg viewBox="0 0 24 24"><path fill="var(--muted)" d="M6.6 10.8a15.1 15.1 0 0 0 6.6 6.6l2.2-2.2a1 1 0 0 1 1-.25 11.4 11.4 0 0 0 3.6.57 1 1 0 0 1 1 1V20a1 1 0 0 1-1 1A17 17 0 0 1 3 4a1 1 0 0 1 1-1h3.5a1 1 0 0 1 1 1c0 1.25.2 2.45.57 3.57a1 1 0 0 1-.25 1z"/></svg>
        0472 639 208
      </p>
      <p class="contact-line">
        <svg viewBox="0 0 24 24"><path fill="var(--muted)" d="M2 5h20v14H2z M4 7v.5l8 5 8-5V7z"/></svg>
        dwalsh@amberfieldcourt.com.au
      </p>
      <p class="address">37 Marrabel Crescent<br>Brindle Vale, Qld 4093</p>
    </div>

    <div class="back-brand">
      <span class="brand-dot"></span>
      <span class="brand-name">Amberfield<br>Court</span>
    </div>
  </section>

</body>
</html>
```